Brochure 11 x 25.5 Trifold

Harbor Lane Associates, Inc. is a payroll, benefits, and HR administration company. We are in need of a brochure to showcase all of our services. Attached is a one-page information sheet that contains the information we want in the brochure as well as several images. The brochure is a 11 x 25.5 tri-fold (a sample is attached). Please use the colors in the attached logo and design to complement our website harborlanehq.com.
Target Market(s)
Company executives
Industry/Entity Type
Human Resource Management
Font styles to use
Other font styles liked:
- Avenir LT
Colors
Designer to choose colors to be used in the design.

```html
<!DOCTYPE html>
<html lang="en">
<head>
<meta charset="utf-8">
<title>Harbor Lane Associates — Trifold Brochure</title>
<link href="https://fonts.googleapis.com/css2?family=Montserrat:ital,wght@0,300;0,400;0,600;0,700;0,800;1,600;1,700&family=Barlow+Condensed:wght@600;700&display=swap" rel="stylesheet">
<style>
:root{
  --navy:#0c3b5c;
  --blue:#1d5b7d;
  --green:#8db33a;
  --green-dark:#74982a;
  --paper:#f2f3f3;
  --paper-2:#e6e8e8;
  --ink:#3d4a52;
  --orange:#e98a2b;
  --gold:#d8a62b;
  --teal:#2f8f9d;
  --red:#d95b3b;
  --sky:#3c8fc2;
  --stage:#2b2b2b;
}
*{box-sizing:border-box;margin:0;padding:0}
html,body{width:1200px;height:1143px;overflow:hidden;background:var(--stage)}
body{position:relative;font-family:'Montserrat',sans-serif;color:var(--ink)}
.spread{position:absolute;left:20px;width:1160px;height:500px;display:flex;background:var(--paper);overflow:hidden}
.spread--outside{top:36px}
.spread--inside{top:576px}
.panel{position:relative;width:386.67px;height:100%;overflow:hidden}
.panel + .panel{border-left:1px solid rgba(0,0,0,.06)}
.fill{position:absolute}

/* outside: intro panel */
.intro-band{position:absolute;left:0;top:0;width:100%;height:215px;background:var(--blue);border-bottom-right-radius:60px}
.intro-heading{position:absolute;left:34px;top:46px;padding-left:10px;border-left:2px solid var(--green)}
.intro-heading .lead{display:block;color:var(--green);font-weight:300;font-size:21px}
.intro-heading .strong{display:block;color:#fff;font-weight:800;font-size:21px;letter-spacing:.3px}
.intro-text{position:absolute;left:34px;top:120px;width:320px;color:#fff;font-size:7.6px;line-height:1.5}
.lifecycle{position:absolute;left:0;top:215px;width:100%;height:285px}
.stage-label{position:absolute;font-size:7px;line-height:1.3;color:#6b757b;width:95px}
.stage-label b{display:block;font-size:8px;font-weight:600;letter-spacing:.4px}

/* outside: contact panel */
.photo{position:absolute;border-radius:34px}
.contact-card{position:absolute;left:18px;top:232px;width:340px;height:240px;background:var(--green);border-radius:34px;color:#fff;padding:34px 40px}
.contact-card h2{font-size:19px;font-weight:600;padding-bottom:6px;border-bottom:1px solid rgba(255,255,255,.7);width:150px;margin-bottom:16px}
.contact-row{display:flex;gap:9px;align-items:flex-start;font-size:8.5px;line-height:1.45;margin-bottom:12px}
.contact-row svg{flex:none;margin-top:1px}

/* cover */
.brand{position:absolute;left:40px;top:30px;display:flex;align-items:center;gap:9px}
.brand-mark{width:20px;height:20px;border-radius:50%;background:var(--green)}
.brand-name{font-size:15px;font-weight:400;color:var(--navy);letter-spacing:.6px;line-height:1.05}
.cover-blob{position:absolute;right:-40px;top:-40px;width:120px;height:110px;background:var(--green);border-radius:50%}
.cover-blob--low{right:-60px;top:auto;bottom:60px;width:90px;height:140px}
.cover-photo{position:absolute;left:26px;top:72px;width:335px;height:200px;border-radius:44px 44px 0 0}
.cover-panel{position:absolute;left:26px;top:250px;width:335px;height:150px;background:var(--navy);border-radius:0 0 44px 44px;padding:28px 36px}
.tagline{border-left:2px solid var(--green);padding-left:8px}
.tagline .t1{display:block;color:#fff;font-weight:300;font-size:17px}
.tagline .t2{display:block;color:#fff;font-weight:800;font-size:17px}
.tagline .t3{display:block;color:var(--green);font-family:'Barlow Condensed',sans-serif;font-weight:700;font-size:25px;letter-spacing:.4px}
.cover-url{position:absolute;left:0;right:0;top:430px;text-align:center;font-size:10px;letter-spacing:1.6px;color:var(--navy);font-weight:600}
.cover-url span{color:var(--green)}

/* inside: sets apart */
.screen-shot{position:absolute;left:40px;top:30px;width:230px;height:150px;border-radius:10px}
.phone-shot{position:absolute;left:240px;top:75px;width:62px;height:120px;border-radius:10px}
.apart-band{position:absolute;left:0;top:0;width:100%;height:100%}
.apart-title{position:absolute;left:34px;top:232px;font-size:19px;color:#fff;font-weight:400;padding-bottom:8px;border-bottom:1px solid rgba(255,255,255,.4);width:310px}
.apart-title b{color:var(--green);font-weight:700}
.apart-grid{position:absolute;left:28px;top:282px;width:335px;display:grid;grid-template-columns:1fr 1fr;gap:16px 14px}
.apart-item{display:flex;gap:8px;align-items:flex-start;font-size:6.4px;line-height:1.4;color:#fff}
.apart-item em{font-style:normal;color:var(--green);font-weight:600}
.dot-icon{flex:none;width:30px;height:30px;border-radius:50%;background:var(--green);display:flex;align-items:center;justify-content:center}

/* services */
.services-title{position:absolute;left:30px;top:18px;font-size:22px;font-style:italic;font-weight:600;color:var(--green)}
.services-title b{color:var(--navy);font-weight:700}
.card-grid{position:absolute;left:22px;top:62px;width:344px;display:grid;grid-template-columns:1fr 1fr;gap:10px 12px}
.card{position:relative;background:#fff;border-radius:12px;box-shadow:0 2px 6px rgba(0,0,0,.12);overflow:hidden;height:128px}
.card-head{background:var(--navy);color:var(--green);font-weight:700;font-style:italic;font-size:11px;line-height:1.1;padding:8px 36px 7px 10px;min-height:34px;display:flex;align-items:center}
.card-icon{position:absolute;right:7px;top:6px;width:22px;height:22px;border-radius:50%;border:1.5px solid var(--green);background:var(--navy)}
.card ul{list-style:none;padding:7px 8px 0 10px}
.card li{font-size:6.3px;line-height:1.45;color:#4a555b;padding-left:8px;position:relative}
.card li::before{content:"";position:absolute;left:0;top:2.5px;width:4px;height:4px;border-radius:50%;border:1px solid var(--green)}
.card--short{height:108px}
.back-brand{position:absolute;left:212px;top:146px;width:160px}
.back-brand .brand-name{font-size:11px}
.back-brand h3{margin-top:10px;font-size:12px;font-weight:800;color:var(--navy);line-height:1.15;text-transform:uppercase}
.back-brand h3 span{color:var(--green);font-weight:400}
.team-photo{position:absolute;left:0;top:262px;width:100%;height:226px}
.bottom-rule{position:absolute;left:0;bottom:0;width:100%;height:12px;background:var(--green)}
</style>
</head>
<body>

<section class="spread spread--outside">

  <div class="panel panel--intro">
    <div class="intro-band"></div>
    <h2 class="intro-heading"><span class="lead">From hire to retire,</span><span class="strong">we've got you covered</span></h2>
    <p class="intro-text">Harbor Lane Associates has been delivering quality HR and Payroll services for over 25 years. Our dedicated team of professionals is focused on being the best service provider in the industry. Our goal is to relieve business executives of the challenges of managing a dynamic and growing workforce in today's regulatory environment and give them the freedom to focus on what drives their business.</p>
    <div class="lifecycle">
      <svg width="387" height="285" viewBox="0 0 387 285" aria-hidden="true">
        <defs>
          <marker id="arrowhead" viewBox="0 0 10 10" refX="5" refY="5" markerWidth="5" markerHeight="5" orient="auto"><path d="M0 0L10 5L0 10z" fill="context-stroke"/></marker>
        </defs>
        <g fill="none" stroke-width="2" marker-end="url(#arrowhead)">
          <path d="M160 95 A62 62 0 0 1 222 88" stroke="var(--orange)"/>
          <path d="M238 98 A62 62 0 0 1 258 140" stroke="var(--gold)"/>
          <path d="M258 158 A62 62 0 0 1 238 196" stroke="var(--sky)"/>
          <path d="M222 206 A62 62 0 0 1 170 208" stroke="var(--teal)"/>
          <path d="M152 198 A62 62 0 0 1 135 155" stroke="var(--blue)"/>
          <path d="M135 138 A62 62 0 0 1 148 104" stroke="var(--red)"/>
        </g>
        <text x="196" y="146" text-anchor="middle" font-family="Montserrat, sans-serif" font-size="10" fill="#6b757b">EMPLOYEE</text>
        <text x="196" y="158" text-anchor="middle" font-family="Montserrat, sans-serif" font-size="10" font-weight="700" fill="#6b757b">LIFECYCLE</text>
      </svg>
      <div class="stage-label" style="left:150px;top:8px"><b style="color:var(--orange)">HIRING</b>Integrated cloud-based ATS. Auto post to job boards, applicant management and screening</div>
      <div class="stage-label" style="left:272px;top:38px"><b style="color:var(--gold)">ONBOARDING</b>Auto generate notice to new hire, standard and customized forms and acknowledgements</div>
      <div class="stage-label" style="left:286px;top:130px"><b style="color:var(--sky)">PAYROLL</b>HRIS, Direct deposits, New Hire Reporting, Employee Portal, Year End Reporting</div>
      <div class="stage-label" style="left:250px;top:212px"><b style="color:var(--teal)">BENEFITS</b>Online enrollment, benefit application, eligibility reconciliations, tracking notifications, retirement plan</div>
      <div class="stage-label" style="left:34px;top:192px;width:100px"><b style="color:var(--blue)">EMPLOYEE MANAGEMENT</b>Culture, development, discipline, leave management, Workers' Compensation claims, employee verifications, handbook</div>
      <div class="stage-label" style="left:30px;top:110px"><b style="color:var(--red)">SEPARATION</b>COBRA, Retirement plan assistance, DOL Noticing</div>
    </div>
  </div>

  <div class="panel panel--contact">
    <div class="fill" role="img" aria-label="Faded photo of colleagues in an office" style="left:0;top:0;width:110px;height:260px;background:linear-gradient(180deg,#d9dbdb,#ececec)"></div>
    <div class="photo" role="img" aria-label="Photo of a consultant meeting with a client across a desk" style="left:60px;top:22px;width:300px;height:190px;background:linear-gradient(135deg,#3a3f44 0%,#6e6660 45%,#b7a99a 100%)"></div>
    <div class="fill" style="right:-30px;top:180px;width:70px;height:210px;background:var(--blue);border-radius:40px 0 0 40px"></div>
    <div class="contact-card">
      <h2>Get In Touch</h2>
      <div class="contact-row">
        <svg width="10" height="12" viewBox="0 0 10 12"><path d="M5 0.6a4 4 0 0 1 4 4c0 3-4 6.8-4 6.8S1 7.6 1 4.6a4 4 0 0 1 4-4z" fill="none" stroke="#fff"/><circle cx="5" cy="4.6" r="1.4" fill="#fff"/></svg>
        <span>412 Harbor Point Drive<br>Riverton, LA 70000</span>
      </div>
      <div class="contact-row">
        <svg width="10" height="10" viewBox="0 0 10 10"><path d="M2 1l2 2-1 1.4a6 6 0 0 0 2.6 2.6L7 6l2 2-1.3 1.3C4.5 9 1 5.5.7 2.3z" fill="none" stroke="#fff"/></svg>
        <span>555-010-3000<br>1-800-555-0142<br>555-010-1488</span>
      </div>
      <div class="contact-row">
        <svg width="10" height="10" viewBox="0 0 10 10"><rect x=".5" y="2" width="9" height="6.5" rx="1" fill="none" stroke="#fff"/><path d="M.8 2.4L5 5.6l4.2-3.2" fill="none" stroke="#fff"/></svg>
        <span>info@harborlanehq.com<br>www.HarborLaneHQ.com</span>
      </div>
    </div>
  </div>

  <div class="panel panel--cover">
    <div class="cover-blob"></div>
    <div class="cover-blob cover-blob--low"></div>
    <div class="brand"><span class="brand-mark"></span><span class="brand-name">HARBOR LANE<br>ASSOCIATES</span></div>
    <div class="cover-photo" role="img" aria-label="Photo of a cheerful professional celebrating at a laptop in a bright office" style="background:linear-gradient(120deg,#e9702a 0%,#f2b534 30%,#4a3b33 65%,#2a2522 100%)"></div>
    <div class="cover-panel">
      <p class="tagline"><span class="t1">Your single-source</span><span class="t2">solution for</span><span class="t3">ENTIRE EMPLOYEE</span></p>
    </div>
    <p class="cover-url">www.<span>HarborLane</span>HQ.com</p>
  </div>
</section>

<section class="spread spread--inside">

  <div class="panel panel--apart">
    <svg class="apart-band" viewBox="0 0 387 500" preserveAspectRatio="none" aria-hidden="true"><path d="M0 175 L387 205 L387 500 L0 500z" fill="var(--navy)"/></svg>
    <div class="screen-shot" role="img" aria-label="Screenshot of the online HR and payroll dashboard on a monitor" style="background:linear-gradient(180deg,#1f1f22 0 8px,#f7f8f9 8px,#e3e8ec 100%);border:5px solid #1f1f22"></div>
    <div class="phone-shot" role="img" aria-label="Screenshot of the employee mobile app on a phone" style="background:linear-gradient(180deg,#e9eef2,#9fb6c8);border:3px solid #d8dadc"></div>
    <h2 class="apart-title">What <b>Sets Us Apart?</b></h2>
    <div class="apart-grid">
      <div class="apart-item"><span class="dot-icon"></span><p>Our <em>dedicated team of experts</em> is always just a call or email away. You get direct phone numbers to the professionals you need.</p></div>
      <div class="apart-item"><span class="dot-icon"></span><p>Our <em>advanced software</em> is used to process payroll for many companies and millions of employees nationwide, making complex payrolls easy.</p></div>
      <div class="apart-item"><span class="dot-icon"></span><p><em>Access your employee information how you need it, when you need it</em> with our quick-access reports and intuitive report writer.</p></div>
      <div class="apart-item"><span class="dot-icon"></span><p>We are equipped with <em>education, experience, certifications and motivation.</em> Our staff operates at the highest level every day.</p></div>
      <div class="apart-item"><span class="dot-icon"></span><p>Employee information is automatically integrated across all modules, <em>eliminating duplicate data entry and significantly reducing errors.</em></p></div>
      <div class="apart-item"><span class="dot-icon"></span><p>Our <em>client branded, cloud-based Employee and Manager portals</em> give your team secure access to payroll information.</p></div>
    </div>
  </div>

  <div class="panel panel--services">
    <h2 class="services-title">Our <b>Services</b></h2>
    <div class="card-grid">
      <article class="card"><span class="card-icon"></span><h3 class="card-head">Payroll</h3><ul><li>Fast, efficient, accurate</li><li>Paper checks or direct deposit</li><li>Easy time file uploads or integrated time clock options</li><li>New hire reporting</li><li>Custom GL file</li><li>Comprehensive reporting options</li><li>Certified payroll option</li></ul></article>
      <article class="card"><span class="card-icon"></span><h3 class="card-head">Human Resource Administration</h3><ul><li>Wage and hour compliance</li><li>Employee handbooks</li><li>Performance management</li><li>Employee discipline and termination counseling</li><li>Unemployment claims administration</li><li>Manager training</li></ul></article>
      <article class="card"><span class="card-icon"></span><h3 class="card-head">Benefits Management</h3><ul><li>Customized benefits packet</li><li>Track new hire eligibility</li><li>Open enrollment assistance</li><li>Electronic enrollment</li><li>Track and submit enrollments</li><li>Provide 401k census report</li><li>Remit retirement plan reports and funds</li><li>ACA compliance</li></ul></article>
      <article class="card"><span class="card-icon"></span><h3 class="card-head">Time and Attendance</h3><ul><li>Integrated with payroll</li><li>Mobile and geofencing options</li><li>Overtime alerts</li><li>Online time-off requests</li><li>Swipe and proximity clocks</li><li>Biometric clocks</li><li>PTO tracking</li></ul></article>
      <article class="card"><span class="card-icon"></span><h3 class="card-head">Employee Onboarding</h3><ul><li>Simple, accurate, paperless</li><li>Custom forms and acknowledgements</li><li>Standard forms (W-4, I-9, state withholding)</li><li>Paperless electronic signatures</li><li>Employee handbook and policy acknowledgements</li><li>Custom welcome videos</li></ul></article>
      <article class="card"><span class="card-icon"></span><h3 class="card-head">Talent Acquisition</h3><ul><li>Custom careers page</li><li>Standard or custom job applications</li><li>Easy conversion of applicant data</li><li>Review, rate and contact applicants</li><li>Mobile-friendly access</li><li>Easy posting to top job boards</li><li>Candidate screening</li></ul></article>
    </div>
  </div>

  <div class="panel panel--more">
    <div class="card-grid" style="top:18px;width:344px">
      <article class="card card--short"><span class="card-icon"></span><h3 class="card-head">COBRA Administration</h3><ul><li>Initial notices</li><li>Open enrollment notices</li><li>Daily 24/7 online reporting</li><li>Qualified beneficiary election notices</li><li>Premium collection</li><li>Access to professionals</li></ul></article>
      <article class="card card--short"><span class="card-icon"></span><h3 class="card-head">Cafeteria Plan / FSA Administration</h3><ul><li>Plan documents</li><li>Online claims</li><li>Debit cards</li><li>Annual testing</li></ul></article>
      <article class="card" style="height:128px"><span class="card-icon"></span><h3 class="card-head">Compliance</h3><ul><li>Certified experts ensure compliance with all laws</li><li>COBRA reporting</li><li>Affirmative Action</li><li>Affordable Care Act</li><li>Family Medical Leave Act</li><li>Workers' Comp audits</li></ul></article>
    </div>
    <div class="back-brand">
      <div class="brand" style="position:static"><span class="brand-mark" style="width:14px;height:14px"></span><span class="brand-name">HARBOR LANE<br>ASSOCIATES</span></div>
      <h3><span>Save time and stay focused on</span><br>running your business</h3>
    </div>
    <div class="team-photo" role="img" aria-label="Photo of business professionals shaking hands across a meeting table" style="background:linear-gradient(110deg,#f4f4f4 0%,#c9ced3 30%,#3a3f48 55%,#8a8f96 80%,#e8e8e8 100%)"></div>
    <div class="bottom-rule"></div>
  </div>
</section>

</body>
</html>
```